Our companies name is The Gilded Ladle and we specialize in craft cupcakes, what I mean by that is that we bake our cupcakes with craft beer and other alcoholic drinks. We are trying to focus on being elegant but at the same time unpretentious. Since we are incorporating beer in our cupcakes we want the business card to have our logo in the front and our information in the back.

Once we select the best design we will provide the contact information to be added. Thank you.

Industry/Entity Type

Business

Font styles to use
Decorative
Script

Requirements
Must have
• Round corners
Should not have
• Square corners

```html
<!DOCTYPE html>
<html lang="en">
<head>
<meta charset="utf-8">
<title>The Gilded Ladle – Business Card</title>
<link rel="stylesheet" href="https://fonts.googleapis.com/css2?family=Exo+2:wght@300;400;600&display=swap">
<style>
  :root {
    --backdrop: #ebe8e3;
    --card-white: #ffffff;
    --card-shade: #e6e6e6;
    --teal: #86cfc4;
    --accent-red: #e8262f;
    --ink: #1f2a2b;
    --text-light: #ffffff;
  }
  html, body {
    margin: 0;
    padding: 0;
    width: 1200px;
    height: 828px;
    overflow: hidden;
    background: var(--backdrop);
    font-family: "Exo 2", sans-serif;
  }
  .canvas {
    position: relative;
    width: 1200px;
    height: 828px;
    display: flex;
    align-items: center;
    justify-content: center;
    gap: 40px;
  }
  .card {
    width: 540px;
    height: 310px;
    border-radius: 18px;
    overflow: hidden;
    box-shadow: 0 6px 18px rgba(0,0,0,0.12);
    background: var(--card-white);
  }
  .card svg { display: block; width: 100%; height: 100%; }
  .brand-name { font-family: "Exo 2", sans-serif; font-weight: 600; fill: var(--ink); }
  .web-address { font-weight: 400; fill: var(--text-light); letter-spacing: 4px; }
  .person-name { font-weight: 400; fill: var(--text-light); letter-spacing: 1.5px; }
  .person-title { font-weight: 300; fill: var(--text-light); }
  .contact-line { font-weight: 300; fill: var(--text-light); }
  .icon { fill: none; stroke: var(--text-light); stroke-width: 1.3; }
</style>
</head>
<body>
<main class="canvas">

  <section class="card card-front" aria-label="Card front">
    <svg viewBox="0 0 540 310" xmlns="http://www.w3.org/2000/svg">
      <defs>
        <radialGradient id="frontWhite" cx="0.4" cy="0.35" r="0.8">
          <stop offset="0" stop-color="var(--card-white)"/>
          <stop offset="1" stop-color="var(--card-shade)"/>
        </radialGradient>
      </defs>
      <rect class="front-base" width="540" height="310" fill="url(#frontWhite)"/>
      <path class="front-band" d="M0,246 Q420,230 490,0 L540,0 L540,310 L0,310 Z" fill="var(--teal)"/>
      <path class="front-curve" d="M0,246 Q420,230 490,0" fill="none" stroke="var(--accent-red)" stroke-width="6"/>
      <g class="brand-mark">
        <circle cx="126" cy="113" r="12" fill="var(--ink)"/>
        <text class="brand-name" x="146" y="120" font-size="20">The Gilded Ladle</text>
      </g>
      <text class="web-address" x="490" y="284" font-size="15" text-anchor="end">www.gildedladle.com</text>
    </svg>
  </section>

  <section class="card card-back" aria-label="Card back">
    <svg viewBox="0 0 540 310" xmlns="http://www.w3.org/2000/svg">
      <defs>
        <radialGradient id="backWhite" cx="0.3" cy="0.7" r="0.7">
          <stop offset="0" stop-color="var(--card-white)"/>
          <stop offset="1" stop-color="var(--card-shade)"/>
        </radialGradient>
      </defs>
      <rect class="back-base" width="540" height="310" fill="var(--teal)"/>
      <path class="back-panel" d="M0,92 Q290,80 350,310 L0,310 Z" fill="url(#backWhite)"/>
      <path class="back-curve" d="M0,92 Q290,80 350,310" fill="none" stroke="var(--accent-red)" stroke-width="6"/>
      <g class="brand-mark">
        <circle cx="72" cy="218" r="12" fill="var(--ink)"/>
        <text class="brand-name" x="92" y="225" font-size="19">The Gilded Ladle</text>
      </g>

      <g class="contact-block" text-anchor="end">
        <text class="person-name" x="510" y="40" font-size="18">MARA ELLISON</text>
        <text class="person-title" x="510" y="60" font-size="12.5">Managing Director</text>

        <text class="contact-line" x="490" y="104" font-size="12">27 Harbor Lane, Suite 4</text>
        <text class="contact-line" x="490" y="121" font-size="12">Brookfield, OR 97201</text>

        <text class="contact-line" x="490" y="156" font-size="12">014 552 7190</text>
        <text class="contact-line" x="490" y="176" font-size="12">014 552 7191</text>
        <text class="contact-line" x="490" y="196" font-size="12">014 552 7192</text>
        <text class="contact-line" x="490" y="216" font-size="12">hello@gildedladle.com</text>
        <text class="contact-line" x="490" y="236" font-size="12">www.gildedladle.com</text>
      </g>

      <g class="contact-icons">
        <path class="icon" d="M500,146 q0,8 8,10 l2,-3 -3,-2 -1,1 q-3,-1 -4,-4 l1,-1 -2,-3 z"/>
        <rect class="icon" x="502" y="165" width="7" height="12" rx="1.2"/>
        <rect class="icon" x="500" y="188" width="11" height="8" rx="1"/>
        <rect class="icon" x="502" y="185" width="7" height="3"/>
        <rect class="icon" x="500" y="207" width="11" height="8" rx="1"/>
        <path class="icon" d="M500,207 l5.5,4.5 5.5,-4.5"/>
        <circle class="icon" cx="505.5" cy="232" r="5.5"/>
        <path class="icon" d="M500,232 h11 M505.5,226.5 q-3,5.5 0,11 M505.5,226.5 q3,5.5 0,11"/>
      </g>
    </svg>
  </section>

</main>
</body>
</html>
```